Brookvale Building Company - advertisement poster

I am looking to print some canvas signs to advertise my general contracting company, Brookvale Building Company. The sign will measure 6' long x 3' high so the size should match that ratio. I already have a logo icon, which is the Letter 'B' and some trees that I would like to incorporate, see attached. I would also like the to have the following information listed:
1) phone number: 831-555-0172
2) email: brookvalebuildingcompany@mailnest.example
3) website: brookvalebuildingcompany.example
4) Lic#4826130
5) I want to use this text: "BUILD WITH THE B-CREW!"

The ad should be relatively simple and clean. Black and Green are my company colors. I am open to creative ideas!

Target Market(s)

People looking to renovate their homes

Industry/Entity Type

Construction

Colors
59FF00
82FF00
B8FF75
E3FFCB
F4FFEA

Requirements
Must have
• Must have my company logo
Should not have
• No photos or complex graphics

```html
<!DOCTYPE html>
<html lang="en">
<head>
<meta charset="utf-8">
<title>Brookvale Building Company – Sign</title>
<link href="https://fonts.googleapis.com/css2?family=Poppins:wght@300;400;600;700&display=swap" rel="stylesheet">
<style>
  :root {
    --page: #e6e6e6;
    --ink: #050705;
    --green: #59ff00;
    --green-mid: #82ff00;
    --green-soft: #b8ff75;
    --green-pale: #e3ffcb;
    --green-line: #5fc92f;
    --white: #ffffff;
  }
  html, body {
    margin: 0;
    width: 1200px;
    height: 1200px;
    overflow: hidden;
    background: var(--page);
    font-family: "Poppins", sans-serif;
  }
  .sign {
    position: absolute;
    left: 114px;
    top: 357px;
    width: 972px;
    height: 486px;
    overflow: hidden;
    background:
      radial-gradient(ellipse at 48% 40%, #1c2a1a 0%, #0c130b 45%, var(--ink) 80%);
  }
  .headline {
    position: absolute;
    left: 46px;
    top: 22px;
    margin: 0;
    font-weight: 600;
    font-size: 242px;
    line-height: 1;
    letter-spacing: 4px;
    background: linear-gradient(180deg, var(--white) 12%, var(--green-pale) 30%, var(--green-soft) 52%, var(--green) 82%);
    -webkit-background-clip: text;
    background-clip: text;
    color: transparent;
    -webkit-text-stroke: 3px var(--green-line);
  }
  .tagline {
    position: absolute;
    left: 52px;
    top: 238px;
    margin: 0;
    font-size: 70px;
    line-height: 1;
    font-weight: 400;
    color: var(--white);
    white-space: nowrap;
  }
  .tagline .crew { color: var(--green); font-weight: 600; }
  .license {
    position: absolute;
    left: 782px;
    top: 75px;
    width: 139px;
    height: 27px;
    border: 1.5px solid var(--green-line);
    border-radius: 5px;
    color: var(--green-line);
    font-weight: 600;
    font-size: 17px;
    line-height: 27px;
    text-align: center;
  }
  .brand {
    position: absolute;
    left: 54px;
    top: 338px;
    width: 190px;
    text-align: center;
  }
  .brand-mark {
    display: block;
    width: 58px;
    height: 58px;
    margin: 0 auto 10px;
    background: var(--green-line);
  }
  .brand-name {
    margin: 0;
    font-weight: 600;
    font-size: 18px;
    line-height: 1.2;
    color: var(--white);
  }
  .contact {
    position: absolute;
    left: 291px;
    top: 382px;
    color: var(--white);
  }
  .phone {
    display: flex;
    align-items: center;
    gap: 6px;
    font-weight: 600;
    font-size: 39px;
    line-height: 1;
  }
  .line {
    display: flex;
    align-items: center;
    gap: 4px;
    font-weight: 300;
    font-size: 15px;
    margin-top: 6px;
  }
  .icon { flex: none; }
  .corner {
    position: absolute;
    left: 0;
    top: 0;
  }
</style>
</head>
<body>
  <section class="sign">
    <svg class="corner" width="972" height="486" viewBox="0 0 972 486">
      <defs>
        <linearGradient id="cornerFill" x1="0" y1="1" x2="1" y2="0">
          <stop offset="0" stop-color="#0a4a05"/>
          <stop offset="0.55" stop-color="#169a10"/>
          <stop offset="1" stop-color="#22d01a"/>
        </linearGradient>
      </defs>
      <polyline points="622,486 966,252 972,256" fill="none" stroke="#1cbf12" stroke-width="3"/>
      <polygon role="img" aria-label="Green angled panel with a fine grid texture" points="666,486 972,279 972,486" fill="url(#cornerFill)"/>
      <line x1="780" y1="486" x2="972" y2="380" stroke="#3fe53a" stroke-width="2" opacity="0.7"/>
    </svg>

    <h1 class="headline">BUILD</h1>
    <p class="tagline">WITH THE <span class="crew">B-CREW!</span></p>

    <div class="license">LIC#4826130</div>

    <div class="brand">
      <span class="brand-mark"></span>
      <p class="brand-name">Brookvale Building Company</p>
    </div>

    <div class="contact">
      <div class="phone">
        <svg class="icon" width="28" height="28" viewBox="0 0 28 28">
          <circle cx="14" cy="14" r="14" fill="#5fc92f"/>
          <path d="M9.5 7.5l3 3-1.6 1.8c.9 1.9 2.3 3.4 4.3 4.4l1.8-1.6 3 3-2 2c-5 0-10.5-5.5-10.5-10.6z" fill="#0a0f0a"/>
        </svg>
        <span>831-555-0172</span>
      </div>
      <div class="line">
        <svg class="icon" width="15" height="15" viewBox="0 0 16 16">
          <circle cx="8" cy="8" r="8" fill="#5fc92f"/>
          <rect x="3.5" y="5" width="9" height="6" fill="none" stroke="#0a0f0a" stroke-width="1"/>
          <path d="M3.5 5l4.5 3.5L12.5 5" fill="none" stroke="#0a0f0a" stroke-width="1"/>
        </svg>
        <span>brookvalebuildingcompany@mailnest.example</span>
      </div>
      <div class="line">
        <svg class="icon" width="15" height="15" viewBox="0 0 16 16">
          <circle cx="8" cy="8" r="6" fill="none" stroke="#5fc92f" stroke-width="1.4"/>
          <ellipse cx="8" cy="8" rx="2.6" ry="6" fill="none" stroke="#5fc92f" stroke-width="1"/>
          <line x1="2" y1="8" x2="14" y2="8" stroke="#5fc92f" stroke-width="1"/>
        </svg>
        <span>brookvalebuildingcompany.example</span>
      </div>
    </div>
  </section>
</body>
</html>
```